Modern corporate presentation

We need a clean, restrained company presentation in a modern Prezi style (design templates are attached for orientation). Please see the attachment for the briefing, colors and our corporate design.

content 1
Title:

FILOVAN
We connect worlds.
Digitization = increase in customer satisfaction

content 2
Animated on photo of company building (photo attached)

Text:

As Europe's leading service provider for business process outsourcing, we optimize your document management along the entire process chain of your document cycles, including physical long-term archiving after processing - efficiently, flexibly, individually and transparently!

content 3
Title: History
Overview of history as a timeline (see example design template slide 2) with dates and icons
Text:
1995
1997
2000
2016
2018
2021

content 4 or onwards
Morph transitions / individual seasons
1995 Founded by Lothar Brenner
1997 Start of ARKI@NET development
2000 real start ARKI@NET, certification GoB/S and KVR
2016 Development of Big Data + inMemory searches, first processes with AI
2018
ARKI@NET goes mobile
Expansion of the Siegen site with a new logistics center
Launch Papyrix concept
2021 More than 400 satisfied employees

content 5
Title: Facts and Figures
Animated to morph the following texts/numbers:

family business
400 employees at different locations
Own data centers
7,500 pallet spaces
50,000 active users daily on the ARKI@NET platform
525 000 receipts per month
210 customers from all over Europe
all necessary certifications

content 6
Title: Product and service portfolio
Combine yourself...
Create animation from Lego building blocks, which are put together, morph individually according to the order (1-3).

Module 1:
system platform
• Audit-proof archiving ARKI@NET
• Fully integrated document management
• Complete, certified KVR® integration

Module 2:
solution modules
• Digital files
• Invoice receipt workflow
ordering system
• Digital inbox
• Case management
• Data Lantern

Module 3:

process services
• Storage
• Scanning Service
• Collection Services
• BPO Inbox
• BPO invoice receipt

content 7
Title: Good Reasons / Benefits
Trust / full-service provider for document-based business processes completely own solution
Portfolio / depiction of the entire process chain from a single source
Experience / reference projects of all sizes and industries
Employees / All services are provided by our own staff without the involvement of subcontractors

content 8
Title: The 100% Philosophy

Overview of the following 3 main points, which are highlighted individually below:

The system
Services
Privacy and Certifications
___

The system
• 100% own data center with 24x7 operation, incl. backup data center
• Certified KVR partner
• Real, completely in-house developed SaaS solution for data center operations only
• Maintenance, support and updates included
• Web-based application

Services
• Combination of man & machine
• Service level agreements, service defined in terms of time
• Penalty for non-fulfilment

Privacy and certifications:
• All common certifications
• Own compliance management
• Data protection according to GDPR

Font styles to use
Other font styles liked:
• Myrlad Pro Bold für Head und Sublines, Lucida Grande Regular für Fließtexte

Requirements
Must have
• clean and reserved, taking our corporate design into account
Nice to have
• Prezi Style, seamless transitions (similar to a scrollipage)

```html
<!DOCTYPE html>
<html lang="en">
<head>
<meta charset="utf-8">
<title>FILOVAN – Company Presentation</title>
<link href="https://fonts.googleapis.com/css2?family=Source+Sans+3:wght@400;600;700;800&family=Open+Sans:wght@400;600&display=swap" rel="stylesheet">
<style>
:root{
  --ink:#141414;
  --ink-soft:#2a2a2a;
  --tan:#b3a587;
  --tan-dark:#9a8c6e;
  --paper:#ffffff;
  --canvas:#eceae6;
  --text:#555555;
  --muted:#8a8a8a;
  --line:#d9d6cf;
  --head:"Source Sans 3", "Helvetica Neue", Arial, sans-serif;
  --body:"Open Sans", "Lucida Grande", Arial, sans-serif;
}
*{box-sizing:border-box;margin:0;padding:0}
html,body{width:1200px;height:4040px;overflow:hidden}
body{background:var(--canvas);font-family:var(--body);color:var(--text)}
.deck{display:flex;flex-direction:column;gap:46px;padding:22px 32px}
.slide{position:relative;width:1136px;height:620px;background:var(--paper);overflow:hidden;box-shadow:0 2px 10px rgba(0,0,0,.08)}
.abs{position:absolute}
.slide-title{font-family:var(--head);font-weight:800;color:var(--ink);letter-spacing:.5px;text-transform:uppercase}

/* brand */
.brand{font-family:var(--head);font-weight:400;color:#fff;font-size:52px;letter-spacing:3px}

/* title slide */
.title-sub{left:60px;top:468px;font-family:var(--head);font-size:22px;font-weight:600;color:var(--ink)}
.title-main{left:58px;top:500px;font-size:58px}

/* about slide */
.about-photo{inset:0;background:linear-gradient(180deg,#5d7ea6 0%,#8fa9c7 38%,#c9d3dc 62%,#6f7378 100%)}
.about-card{left:92px;top:96px;width:420px;height:412px;background:#fff;padding:40px 38px;box-shadow:0 4px 18px rgba(0,0,0,.18)}
.about-card p{font-size:15px;line-height:1.6;color:var(--ink-soft);text-align:center}
.value-row{display:flex;gap:34px;margin-top:30px}
.value{display:flex;flex-direction:column;align-items:center;gap:8px;font-size:14px;color:var(--text)}
.value svg{width:40px;height:40px}

/* history */
.history-title{left:0;right:0;top:44px;text-align:center;font-size:38px}
.history-rule{left:380px;right:380px;top:100px;height:2px;background:var(--line)}
.timeline-band{left:40px;top:290px;width:1080px;height:56px}
.timeline-cols{left:40px;top:112px;width:1056px;height:460px;display:grid;grid-template-columns:repeat(6,176px)}
.tl-col{position:relative}
.tl-note{position:absolute;left:10px;width:156px;text-align:center}
.tl-note h3{font-family:var(--head);font-size:15px;font-weight:700;color:var(--ink);margin-bottom:6px}
.tl-note p{font-size:12px;line-height:1.45;color:var(--muted)}
.tl-note.up{top:20px}
.tl-note.down{top:268px}
.tl-icon{position:absolute;left:50px;width:76px;height:76px;border-radius:50%;background:#fff;border:2px solid var(--line);display:flex;align-items:center;justify-content:center}
.tl-icon svg{width:36px;height:36px}
.tl-icon.up{top:70px}
.tl-icon.down{top:280px}
.tl-stem{position:absolute;left:87px;width:2px;background:var(--line)}
.tl-stem.up{top:146px;height:32px}
.tl-stem.down{top:234px;height:46px}

/* facts */
.facts-title{left:62px;top:68px;font-size:36px}
.facts-list{left:64px;top:140px;list-style:none}
.facts-list li{display:flex;align-items:center;gap:14px;font-size:18px;color:var(--ink-soft);height:47px}
.facts-list li::before{content:"";width:9px;height:9px;border-top:3px solid var(--tan);border-right:3px solid var(--tan);transform:rotate(45deg);flex:none}
.facts-photo{left:680px;top:72px;width:390px;height:462px;background:linear-gradient(160deg,#d9cdb4 0%,#b89b62 40%,#5b6470 100%)}

/* benefits */
.benefits-title{left:0;right:0;top:56px;text-align:center;font-size:36px}
.benefit-row{left:104px;top:150px;display:flex;gap:40px}
.benefit{position:relative;width:200px;height:370px;background:#fff;border:1px solid var(--line);box-shadow:0 3px 12px rgba(0,0,0,.08);padding:124px 18px 20px;text-align:center}
.benefit.is-lead{background:var(--tan);border-color:var(--tan)}
.benefit-icon{position:absolute;left:50%;top:22px;transform:translateX(-50%);width:92px;height:92px;border-radius:50%;background:#fff;border:6px solid #efebe3;display:flex;align-items:center;justify-content:center}
.benefit-icon svg{width:42px;height:42px}
.benefit h3{font-family:var(--head);font-size:19px;font-weight:700;color:var(--tan-dark);letter-spacing:.6px;margin-bottom:12px}
.benefit p{font-size:14px;line-height:1.55;color:var(--text)}
.benefit.is-lead h3,.benefit.is-lead p{color:#fff}

/* thank you */
.thanks-text{left:0;right:0;top:90px;text-align:center;font-family:var(--head);font-weight:700;font-size:132px;color:#fff}
.contact-row{left:70px;right:70px;top:478px;display:flex;justify-content:space-between}
.contact{display:flex;gap:16px;align-items:flex-start;width:300px}
.contact svg{width:30px;height:30px;flex:none;margin-top:2px}
.contact strong{display:block;font-family:var(--head);font-size:20px;color:var(--ink);margin-bottom:4px}
.contact span{font-size:16px;color:var(--text)}
</style>
</head>
<body>
<main class="deck">

  <!-- Title -->
  <section class="slide slide-title-page">
    <svg class="abs" style="left:0;top:0" width="1136" height="620" viewBox="0 0 1136 620">
      <defs>
        <linearGradient id="officeTone" x1="0" y1="0" x2="1" y2="1">
          <stop offset="0" stop-color="#e8ecef"/>
          <stop offset=".55" stop-color="#b9c3cc"/>
          <stop offset="1" stop-color="#6e7680"/>
        </linearGradient>
      </defs>
      <path d="M0 0H1136V372C960 452 760 402 560 420C380 436 180 468 0 430Z" fill="var(--ink)"/>
      <path d="M0 430C180 468 380 436 560 420C760 402 960 452 1136 372" fill="none" stroke="#9b9b9b" stroke-width="3"/>
      <g role="img" aria-label="Photo of two business people meeting in a bright office">
        <path d="M640 0H1136V336C980 402 790 398 676 332C590 270 580 90 640 0Z" fill="url(#officeTone)"/>
      </g>
    </svg>
    <div class="brand abs" style="left:60px;top:140px">FILOVAN</div>
    <p class="title-sub abs">Digitization = Increase In Customer Satisfaction</p>
    <h1 class="slide-title title-main abs">We Connect Worlds</h1>
  </section>

  <!-- About -->
  <section class="slide slide-about">
    <div class="about-photo abs" role="img" aria-label="Photo of the company building under a blue sky"></div>
    <div class="about-card abs">
      <p>As Europe's leading service provider for business process outsourcing, we optimize your document management along the entire process chain of your document cycles, including physical long-term archiving after processing.</p>
      <div class="value-row">
        <div class="value">
          <svg viewBox="0 0 40 40" fill="none" stroke="var(--tan)" stroke-width="2"><path d="M6 34V24M14 34V18M22 34V22M30 34V12"/><path d="M6 18L16 10L24 15L34 5M28 5H34V11"/></svg>
          Efficiently
        </div>
        <div class="value">
          <svg viewBox="0 0 40 40" fill="none" stroke="var(--tan)" stroke-width="2"><path d="M20 4V36M4 20H36M20 4L15 9M20 4L25 9M4 20L9 15M4 20L9 25M36 20L31 15M36 20L31 25"/></svg>
          Flexibly
        </div>
        <div class="value">
          <svg viewBox="0 0 40 40" fill="none" stroke="var(--tan)" stroke-width="2"><circle cx="20" cy="10" r="5"/><path d="M11 26C11 19 29 19 29 26V36H11Z"/><circle cx="8" cy="15" r="3"/><circle cx="32" cy="15" r="3"/></svg>
          Individually
        </div>
      </div>
      <div class="value-row" style="margin-top:20px">
        <div class="value">
          <svg viewBox="0 0 40 40" fill="none" stroke="var(--tan)" stroke-width="2"><rect x="6" y="6" width="28" height="28"/><path d="M6 20H34M20 6V34"/></svg>
          Transparently
        </div>
      </div>
    </div>
  </section>

  <!-- History -->
  <section class="slide slide-history">
    <h2 class="slide-title history-title abs">History</h2>
    <div class="history-rule abs"></div>
    <svg class="timeline-band abs" viewBox="0 0 1080 56">
      <polygon points="0,0 170,0 186,28 170,56 0,56" fill="var(--tan)"/>
      <polygon points="176,0 346,0 362,28 346,56 176,56 192,28" fill="var(--ink)"/>
      <polygon points="352,0 522,0 538,28 522,56 352,56 368,28" fill="var(--tan)"/>
      <polygon points="528,0 698,0 714,28 698,56 528,56 544,28" fill="var(--ink)"/>
      <polygon points="704,0 874,0 890,28 874,56 704,56 720,28" fill="var(--tan)"/>
      <polygon points="880,0 1050,0 1066,28 1050,56 880,56 896,28" fill="var(--ink)"/>
      <g font-family="Source Sans 3, Arial, sans-serif" font-weight="700" font-size="22" fill="#fff" text-anchor="middle">
        <text x="90" y="36">1995</text><text x="272" y="36">1997</text><text x="448" y="36">2000</text>
        <text x="624" y="36">2016</text><text x="800" y="36">2018</text><text x="976" y="36">2021</text>
      </g>
    </svg>
    <div class="timeline-cols abs">
      <div class="tl-col">
        <div class="tl-note up"><h3>Key milestone reached</h3><p>A short summary of this year's milestone</p></div>
        <div class="tl-stem down"></div>
        <div class="tl-icon down"><svg viewBox="0 0 36 36" fill="none" stroke="var(--tan)" stroke-width="2"><path d="M4 32V14L18 4L32 14V32Z"/><path d="M14 32V22H22V32"/></svg></div>
      </div>
      <div class="tl-col">
        <div class="tl-icon up"><svg viewBox="0 0 36 36" fill="none" stroke="var(--tan)" stroke-width="2"><path d="M4 32H32M8 32V20M15 32V14M22 32V18M29 32V8"/></svg></div>
        <div class="tl-stem up"></div>
        <div class="tl-note down"><h3>Key milestone reached</h3><p>A short summary of this year's milestone</p></div>
      </div>
      <div class="tl-col">
        <div class="tl-note up"><h3>Key milestone reached</h3><p>A short summary of this year's milestone</p></div>
        <div class="tl-stem down"></div>
        <div class="tl-icon down"><svg viewBox="0 0 36 36" fill="none" stroke="var(--tan)" stroke-width="2"><circle cx="18" cy="14" r="9"/><path d="M12 22L9 33L18 28L27 33L24 22"/></svg></div>
      </div>
      <div class="tl-col">
        <div class="tl-icon up"><svg viewBox="0 0 36 36" fill="none" stroke="var(--tan)" stroke-width="2"><rect x="4" y="6" width="28" height="20"/><path d="M12 32H24M18 26V32M9 20L15 14L20 18L27 11"/></svg></div>
        <div class="tl-stem up"></div>
        <div class="tl-note down"><h3>Key milestone reached</h3><p>A short summary of this year's milestone</p></div>
      </div>
      <div class="tl-col">
        <div class="tl-note up"><h3>Key milestone reached</h3><p>A short summary of this year's milestone</p></div>
        <div class="tl-stem down"></div>
        <div class="tl-icon down"><svg viewBox="0 0 36 36" fill="none" stroke="var(--tan)" stroke-width="2"><path d="M18 4A9 9 0 0 1 24 20V25H12V20A9 9 0 0 1 18 4Z"/><path d="M13 29H23M15 33H21"/></svg></div>
      </div>
      <div class="tl-col">
        <div class="tl-icon up"><svg viewBox="0 0 36 36" fill="none" stroke="var(--tan)" stroke-width="2"><circle cx="18" cy="11" r="5"/><circle cx="7" cy="15" r="3.5"/><circle cx="29" cy="15" r="3.5"/><path d="M9 32C9 22 27 22 27 32M1 30C1 23 10 22 11 24M35 30C35 23 26 22 25 24"/></svg></div>
        <div class="tl-stem up"></div>
        <div class="tl-note down"><h3>Key milestone reached</h3><p>A short summary of this year's milestone</p></div>
      </div>
    </div>
  </section>

  <!-- Facts and figures -->
  <section class="slide slide-facts">
    <h2 class="slide-title facts-title abs">Facts and Figures</h2>
    <ul class="facts-list abs">
      <li>Family business</li>
      <li>400 employees at different locations</li>
      <li>Own data centers</li>
      <li>7,500 pallet spaces</li>
      <li>50,000 active users daily on the ARKI@NET platform</li>
      <li>525 000 receipts per month</li>
      <li>210 customers from all over Europe</li>
      <li>All necessary certifications</li>
    </ul>
    <div class="facts-photo abs" role="img" aria-label="Photo of two colleagues working together at a desk"></div>
  </section>

  <!-- Benefits -->
  <section class="slide slide-benefits">
    <h2 class="slide-title benefits-title abs">Good Reasons / Benefits</h2>
    <div class="benefit-row abs">
      <article class="benefit is-lead">
        <div class="benefit-icon"><svg viewBox="0 0 42 42" fill="none" stroke="var(--tan)" stroke-width="2.2"><path d="M21 4L36 10V20C36 30 29 36 21 39C13 36 6 30 6 20V10Z"/><path d="M14 21L19 26L28 16"/></svg></div>
        <h3>TRUST</h3>
        <p>Full-service provider for document-based business processes completely own solution</p>
      </article>
      <article class="benefit">
        <div class="benefit-icon"><svg viewBox="0 0 42 42" fill="none" stroke="var(--tan)" stroke-width="2.2"><rect x="5" y="12" width="32" height="24" rx="2"/><path d="M15 12V7H27V12M5 22H37M19 22V26H23V22"/></svg></div>
        <h3>PORTFOLIO</h3>
        <p>Depiction of the entire process chain from a single source</p>
      </article>
      <article class="benefit">
        <div class="benefit-icon"><svg viewBox="0 0 42 42" fill="none" stroke="var(--tan)" stroke-width="2.2"><circle cx="21" cy="12" r="6"/><path d="M10 36C10 24 32 24 32 36"/><path d="M21 26V36"/></svg></div>
        <h3>EXPERIENCE</h3>
        <p>Reference projects of all sizes and industries</p>
      </article>
      <article class="benefit">
        <div class="benefit-icon"><svg viewBox="0 0 42 42" fill="none" stroke="var(--tan)" stroke-width="2.2"><circle cx="21" cy="13" r="5"/><circle cx="9" cy="17" r="4"/><circle cx="33" cy="17" r="4"/><path d="M12 36C12 25 30 25 30 36M2 33C2 25 11 24 13 27M40 33C40 25 31 24 29 27"/></svg></div>
        <h3>EMPLOYEES</h3>
        <p>All services are provided by our own staff without the involvement of subcontractors</p>
      </article>
    </div>
  </section>

  <!-- Thank you -->
  <section class="slide slide-thanks">
    <svg class="abs" style="left:0;top:0" width="1136" height="620" viewBox="0 0 1136 620">
      <path d="M0 0H1136V330C960 420 760 372 560 392C380 410 180 436 0 400Z" fill="var(--ink)"/>
      <path d="M0 400C180 436 380 410 560 392C760 372 960 420 1136 330" fill="none" stroke="#9b9b9b" stroke-width="3"/>
    </svg>
    <h2 class="thanks-text abs">Thank You</h2>
    <div class="contact-row abs">
      <div class="contact">
        <svg viewBox="0 0 30 30" fill="var(--tan)"><path d="M15 2C9.5 2 6 6 6 11C6 18 15 28 15 28C15 28 24 18 24 11C24 6 20.5 2 15 2ZM15 15A4 4 0 1 1 15 7A4 4 0 0 1 15 15Z"/></svg>
        <div><strong>Address :</strong><span>14 Y, Filovan Street</span></div>
      </div>
      <div class="contact">
        <svg viewBox="0 0 30 30" fill="var(--tan)"><path d="M3 7H27V23H3Z"/><path d="M3 7L15 17L27 7" fill="none" stroke="#fff" stroke-width="2"/></svg>
        <div><strong>Email Us :</strong><span>info@filovan.com.au</span></div>
      </div>
      <div class="contact">
        <svg viewBox="0 0 30 30" fill="var(--tan)"><path d="M8 3L12 3L14 10L11 12C12.5 15.5 14.5 17.5 18 19L20 16L27 18V22C27 25 25 27 22 27C12 26 4 18 3 8C3 5 5 3 8 3Z"/></svg>
        <div><strong>Phone No :</strong><span>+ 1 555 014 2021</span></div>
      </div>
    </div>
  </section>

</main>
</body>
</html>
```